RTavenor Business Cards & Letterhead

I have a logo but need a design for some new business cards. We are a Design-Build Firm that specializes in the design and construction of commercial projects.
the cards need to be professional. no cartoon stuff.
i would like to have the cards in AI format so I can update the card as needed. Logo is provided.
Our Address is: 4187 Marlowe Ct. Apex, North Carolina 27614

```html
<!DOCTYPE html>
<html lang="en">
<head>
<meta charset="utf-8">
<title>RTavenor Business Card</title>
<link href="https://fonts.googleapis.com/css2?family=Open+Sans:wght@400;600;700&display=swap" rel="stylesheet">
<style>
  :root {
    --backdrop: #474747;
    --card-white: #ffffff;
    --card-dark: #222222;
    --card-black: #151515;
    --swoosh-grey: #5c5c5c;
    --brand-grey: #4a4a4a;
    --brand-grey-light: #6e6e6e;
    --brand-blue: #1763b8;
    --text-light: #f2f2f2;
  }
  * { box-sizing: border-box; margin: 0; padding: 0; }
  html, body {
    width: 1200px; height: 801px; overflow: hidden;
    background: var(--backdrop);
    font-family: "Open Sans", Arial, sans-serif;
  }
  .sheet {
    position: relative; width: 1200px; height: 801px;
    display: flex; align-items: center; justify-content: center; gap: 26px;
  }
  .card {
    position: relative; width: 560px; height: 320px;
    border-radius: 18px; overflow: hidden;
    border: 3px solid var(--brand-blue);
    box-shadow: 0 14px 30px rgba(0,0,0,.35);
  }
  .card-front { background: var(--card-white); }
  .card-front .wave { position: absolute; inset: 0; width: 100%; height: 100%; }
  .wave .dark-field { fill: var(--card-dark); }
  .wave .swoosh { fill: var(--swoosh-grey); }

  .wordmark {
    position: absolute; display: flex; align-items: center; gap: 10px;
    font-weight: 700; letter-spacing: 1px; line-height: 1;
  }
  .wordmark .mark-square { display: block; background: var(--brand-blue); }
  .card-front .wordmark { left: 170px; top: 36px; font-size: 40px; color: var(--brand-grey); }
  .card-front .mark-square { width: 28px; height: 28px; }

  .person { position: absolute; left: 26px; top: 118px; }
  .person-name { font-size: 18px; font-weight: 700; color: var(--brand-blue); letter-spacing: .5px; }
  .person-role { font-size: 14px; color: #333; margin-top: 1px; }

  .contact {
    position: absolute; left: 92px; top: 208px;
    color: var(--text-light); font-size: 12px; line-height: 16px;
  }
  .contact-address { margin-bottom: 6px; }
  .contact-line { display: flex; align-items: center; gap: 8px; }
  .contact-line svg { width: 11px; height: 11px; flex: none; }
  .contact-line svg * { fill: var(--brand-blue); }

  .card-back { background: var(--card-black); }
  .card-back .texture {
    position: absolute; inset: 0;
    background: radial-gradient(ellipse at 60% 40%, #262626 0%, #181818 60%, #111111 100%);
  }
  .card-back .wordmark {
    left: 50%; top: 50%; transform: translate(-50%, -50%);
    font-size: 52px; color: var(--brand-grey-light);
  }
  .card-back .mark-square { width: 36px; height: 36px; }
</style>
</head>
<body>
<main class="sheet">
  <section class="card card-front" aria-label="Business card front">
    <svg class="wave" viewBox="0 0 560 320" preserveAspectRatio="none" aria-hidden="true">
      <path class="swoosh" d="M40,204 C150,186 250,190 338,160 C430,128 505,108 552,72 C515,114 444,142 342,172 C244,202 150,200 40,204 Z"/>
      <path class="dark-field" d="M0,214 C120,196 240,202 340,170 C440,138 512,122 560,96 L560,320 L0,320 Z"/>
    </svg>

    <div class="wordmark"><span class="mark-square"></span><span class="wordmark-name">RTAVENOR</span></div>

    <div class="person">
      <p class="person-name">OWEN HARTLEY</p>
      <p class="person-role">Managing Director</p>
    </div>

    <div class="contact">
      <p class="contact-address">4187 Marlowe Ct. Apex,<br>North Carolina 27614</p>
      <p class="contact-line">
        <svg viewBox="0 0 12 12" aria-hidden="true"><path d="M2.4 0.8 L4.4 3.4 L3.3 4.6 C4 6 5.8 7.9 7.3 8.6 L8.5 7.5 L11.2 9.5 L10 11.4 C5.4 11 0.9 6.4 0.6 2 Z"/></svg>
        <span>919 555 0142</span>
      </p>
      <p class="contact-line">
        <svg viewBox="0 0 12 12" aria-hidden="true"><path d="M0.5 2.5 H11.5 V9.5 H0.5 Z M0.5 2.5 L6 7 L11.5 2.5" /></svg>
        <span>info@rtavenor.com</span>
      </p>
      <p class="contact-line">
        <svg viewBox="0 0 12 12" aria-hidden="true"><circle cx="6" cy="6" r="5.5"/></svg>
        <span>www.rtavenor.com</span>
      </p>
    </div>
  </section>

  <section class="card card-back" aria-label="Business card back">
    <div class="texture" role="img" aria-label="Dark embossed repeating brand pattern"></div>
    <div class="wordmark"><span class="mark-square"></span><span class="wordmark-name">RTAVENOR</span></div>
  </section>
</main>
</body>
</html>
```